Global Beard Oil Review Business needs a refresh

topwhiskertonic.net is a global business who's mission is to curate all available beard oils from around the world, review and grade them and present this curated collection to the user of the website.

The scope of this job includes the web site design and the design of a suitable logo to be used in the site header.

The existing site can be seen on http://topwhiskertonic.net, however this is a mock-up only the style and logo should NOT be used. This is to give you an idea of the concept of the site only.

This job is for PSD design only.

See attached design brief for detailed design requirements.
Updates

Project Deadline Extended
Reason: Extending deadline by 5 days to allow for final submissions

Target Market(s)

Men's grooming / retail

Industry/Entity Type

Retail

Number of Pages Required

2 page

Font styles to use
Sans Serif

Requirements
Must have
• 1) Comparison Table
• 2) Side Bar
• 3) Header area
• 4) Photo of Delvin Marsk (attached - can be circular or "cut-out")
• 5) Cool beard-oriented custom design background (e.g., stylistic black/brown on brown/orange beard background. I envision this beard background "drawing" rather than photo based)
• (see attached design requirements for details)
Nice to have
• Signature style writing at top with name "Delvin Marsk"
Should not have
• Do NOT use the look & feel or logo from the existing site.

```html
<!DOCTYPE html>
<html lang="en">
<head>
<meta charset="utf-8">
<title>Top Whisker Tonic – The World's #1 Beard Oil Authority</title>
<link href="https://fonts.googleapis.com/css2?family=Lato:ital,wght@0,400;0,700;0,900;1,400&family=Dancing+Script:wght@500&display=swap" rel="stylesheet">
<style>
:root{
  --orange:#f7941d;
  --wood-dark:#2b2b2b;
  --wood-dark-2:#363636;
  --wood-light:#8a8a8a;
  --wood-light-2:#9c9c9c;
  --panel:#cfcfcf;
  --ink:#333;
  --ink-soft:#555;
  --side:#3a3a3a;
  --side-text:#e8e8e8;
  --white:#fff;
  --black:#0a0a0a;
  --dot-empty:#e4e4e4;
  --dot-gray:#7a7a7a;
}
*{box-sizing:border-box;margin:0;padding:0}
html,body{width:1200px;height:833px;overflow:hidden}
body{position:relative;font-family:'Lato',sans-serif;color:var(--ink);background:var(--wood-dark)}
.abs{position:absolute}
.wood-dark{background:repeating-linear-gradient(90deg,var(--wood-dark) 0 70px,var(--wood-dark-2) 70px 72px,#303030 72px 140px,#1f1f1f 140px 142px)}
.wood-light{background:repeating-linear-gradient(90deg,var(--wood-light) 0 70px,#6f6f6f 70px 72px,var(--wood-light-2) 72px 140px,#777 140px 142px)}
.site-header{left:0;top:0;width:1200px;height:222px}
.brand{left:500px;top:40px;width:200px;text-align:center;color:var(--orange);font-weight:900;font-size:26px;line-height:30px;letter-spacing:1px}
.brand-mark{display:block;margin:0 auto 12px;width:60px;height:60px;border-radius:50%;background:var(--orange)}
.main-nav{left:0;top:180px;width:1200px;height:42px}
.main-nav a{position:absolute;top:0;color:var(--white);text-decoration:none;font-weight:700;font-size:18px;font-variant:small-caps;letter-spacing:.2px}
.main-nav a.active,.main-nav a.hl{color:var(--orange)}
.main-nav a.active::after{content:"";position:absolute;left:0;right:0;top:40px;height:3px;background:var(--orange)}
.content-band{left:0;top:222px;width:1200px;height:456px}
.main-panel{left:160px;top:238px;width:691px;height:424px;background:var(--panel)}
.page-title{left:13px;top:18px;font-size:21px;font-weight:900;font-variant:small-caps;color:#222}
.intro{left:13px;top:47px;width:515px;font-size:9.2px;line-height:17px;color:#333}
.author-photo{left:573px;top:19px;width:88px;height:88px;border-radius:50%;background:radial-gradient(circle at 50% 40%,#9a9a9a,#3a3a3a);border:2px solid #eee}
.author-caption{left:540px;top:116px;width:160px;text-align:center;font-size:10px;font-weight:700;color:#333}
.author-sign{left:540px;top:130px;width:160px;text-align:center;font-family:'Dancing Script',cursive;font-size:12px;color:#444}
.scale-intro{left:76px;top:124px;font-family:'Dancing Script',cursive;font-size:11px;color:#444;transform:rotate(-3deg)}
.scale-arrow{left:176px;top:130px}
.scale-demo{left:268px;top:120px;display:flex;gap:6px}
.scale-demo span{width:26px;height:26px;border-radius:50%;background:var(--orange)}
.scale-demo span.off{background:var(--dot-empty)}
.oil-table{left:14px;top:178px;width:664px;border-collapse:collapse;table-layout:fixed;font-size:8.6px;color:#444}
.oil-table th{font-size:7.5px;font-weight:700;font-variant:small-caps;text-align:left;height:16px;border-bottom:1px solid #555;color:#222;font-size:8px}
.oil-table td{height:38px;vertical-align:middle;line-height:9px}
.bottle{display:block;width:7px;height:22px;border-radius:2px 2px 1px 1px;background:linear-gradient(#222 0 6px,#5a3a1a 6px)}
.rate{display:flex;gap:2.5px}
.rate i{width:10px;height:10px;border-radius:50%;background:var(--dot-gray)}
.rate i.off{background:var(--dot-empty)}
.rate.overall i{background:var(--orange)}
.rate.overall i.off{background:var(--dot-empty)}
.buy-btn{display:inline-block;width:57px;height:16px;line-height:16px;border-radius:8px;background:var(--orange);color:var(--white);font-size:4.8px;font-weight:700;text-align:center;box-shadow:0 1px 1px rgba(0,0,0,.25)}
.view-more{left:319px;top:397px;width:55px;height:18px;background:#7e7e7e;color:#eee;font-size:5.5px;text-align:center;line-height:18px}
.side-box{left:866px;width:172px;background:var(--side);color:var(--side-text)}
.side-box h3{position:absolute;left:7px;top:7px;width:158px;height:19px;border-bottom:1px solid #bbb;font-size:10px;font-weight:700;padding-left:20px}
.side-box h3::before{content:"";position:absolute;left:0;top:0;width:15px;height:15px;background:var(--orange)}
.side-box h3.ring::before{background:none;border:2px solid var(--orange);border-radius:50%}
.post,.comment{position:absolute;left:7px;width:160px;height:56px}
.post .thumb,.comment .avatar{position:absolute;left:0;top:0;width:47px;height:47px}
.post .thumb{background:linear-gradient(135deg,#b07a3a,#4a3520)}
.comment .avatar{background:linear-gradient(135deg,#8a7a6a,#2e2a26)}
.post h4{position:absolute;left:52px;top:0;font-size:8px;font-weight:900;line-height:10px;text-transform:uppercase}
.post .meta{position:absolute;left:52px;font-size:8px;color:#ccc}
.post .meta b{color:var(--orange);font-weight:400}
.post .rule,.comment .rule{position:absolute;left:0;right:0;bottom:0;height:1px;background:#777}
.comment h5{position:absolute;left:52px;top:0;font-size:8px;font-weight:900}
.comment p{position:absolute;left:52px;top:14px;width:110px;font-size:7.6px;line-height:10px;color:#bbb}
.site-footer{left:0;top:678px;width:1200px;height:128px}
.footer-col h6{font-size:11.5px;font-weight:700;font-variant:small-caps;color:var(--white);text-decoration:underline;text-underline-offset:2px}
.footer-col ul{list-style:none;margin-top:7px}
.footer-col li{font-size:8.8px;line-height:13.6px;color:var(--white)}
.footer-col p{font-size:8.4px;line-height:10.5px;color:var(--white);margin-top:7px;width:110px}
.email{display:block;margin-top:6px;width:126px;height:18px;border:1px solid #ddd;color:#bbb;font-size:8px;line-height:16px;padding-left:7px}
.submit{display:block;margin-top:8px;width:57px;height:18px;background:var(--orange);color:var(--white);font-size:6px;font-weight:700;text-align:center;line-height:18px}
.tags{display:flex;flex-wrap:wrap;width:140px;gap:4px;margin-top:9px}
.tags span{background:var(--orange);color:var(--white);font-size:8.6px;padding:0 3px;height:19px;line-height:19px}
.social{display:flex;gap:8px;margin-top:8px}
.social span{width:18px;height:18px;background:var(--orange)}
.copyright{left:0;top:806px;width:1200px;height:27px;background:var(--black);color:var(--white);font-family:Arial,sans-serif;font-size:8.8px;padding:9px 0 0 162px}
</style>
</head>
<body>

<header class="abs site-header wood-dark">
  <div class="abs brand"><span class="brand-mark"></span>Top Whisker Tonic</div>
  <nav class="abs main-nav">
    <a class="active" href="#" style="left:328px">Home</a>
    <a href="#" style="left:415px">Review Methodology</a>
    <a class="hl" href="#" style="left:613px">Charter</a>
    <a href="#" style="left:718px">Blog</a>
    <a href="#" style="left:799px">About Me</a>
  </nav>
</header>

<div class="abs content-band wood-light"></div>

<main class="abs main-panel">
  <h1 class="abs page-title">The World's #1 Beard Oil Authority</h1>
  <p class="abs intro">Here is the master list of beard oils reviewed to date and ranked on our unic <i>“beard scale”</i>. You can link directly to the corresponding review by clicking on the name of the beard oil. In accordance with our charter, we are actively working to locate and review every single beard oil available on the planet Earth, so check back regularly for updates.</p>
  <div class="abs author-photo" role="img" aria-label="Portrait photo of Delvin Marsk"></div>
  <div class="abs author-caption">Global Beard Oil Reviews</div>
  <div class="abs author-sign">- by Delvin Marsk</div>

  <div class="abs scale-intro">Introducing our new “beard scale” rating system</div>
  <svg class="abs scale-arrow" width="90" height="20" viewBox="0 0 90 20"><path d="M2 4 Q40 18 86 12" fill="none" stroke="#444" stroke-width="1"/><path d="M80 8 L87 12 L80 15" fill="none" stroke="#444" stroke-width="1"/></svg>
  <div class="abs scale-demo"><span></span><span></span><span></span><span></span><span class="off"></span></div>

  <table class="abs oil-table">
    <colgroup><col style="width:57px"><col style="width:59px"><col style="width:28px"><col style="width:40px"><col style="width:46px"><col style="width:67px"><col style="width:74px"><col style="width:75px"><col style="width:76px"><col style="width:88px"><col style="width:54px"></colgroup>
    <thead><tr><th>Suplier</th><th>Name</th><th>Oil</th><th>Origin</th><th>Base Oil</th><th>Scent</th><th>Aroma</th><th>Therapeutic Affect</th><th>Value</th><th>Overall</th><th>Link</th></tr></thead>
    <tbody>
      <tr><td>Northfold<br>Beard Co.</td><td>Timberline</td><td><span class="bottle" role="img" aria-label="Bottle"></span></td><td>AU</td><td>Almond</td><td>Tea Tree</td>
        <td><div class="rate"><i></i><i></i><i></i><i></i><i></i></div></td><td><div class="rate"><i></i><i></i><i></i><i></i><i class="off"></i></div></td><td><div class="rate"><i></i><i></i><i></i><i></i><i></i></div></td><td><div class="rate overall"><i></i><i></i><i></i><i></i><i class="off"></i></div></td><td><span class="buy-btn">GET YOURS NOW</span></td></tr>
      <tr><td>Papa Rook<br>Grooming</td><td>Misty Ridge<br>Man<br>Beard Oil</td><td><span class="bottle" role="img" aria-label="Bottle"></span></td><td>AU</td><td>Castor</td><td>Pinewood</td>
        <td><div class="rate"><i></i><i></i><i></i><i></i><i class="off"></i></div></td><td><div class="rate"><i></i><i></i><i></i><i class="off"></i><i class="off"></i></div></td><td><div class="rate"><i></i><i></i><i></i><i></i><i></i></div></td><td><div class="rate overall"><i></i><i></i><i></i><i class="off"></i><i class="off"></i></div></td><td><span class="buy-btn">GET YOURS NOW</span></td></tr>
      <tr><td>Bristle<br>Baron</td><td>Pinecutter</td><td><span class="bottle" role="img" aria-label="Bottle"></span></td><td>USA</td><td>Coconut</td><td>Fir Needle</td>
        <td><div class="rate"><i></i><i></i><i></i><i></i><i></i></div></td><td><div class="rate"><i></i><i></i><i></i><i></i><i class="off"></i></div></td><td><div class="rate"><i></i><i></i><i></i><i></i><i></i></div></td><td><div class="rate overall"><i></i><i></i><i></i><i></i><i class="off"></i></div></td><td><span class="buy-btn">GET YOURS NOW</span></td></tr>
      <tr><td>Bravarian<br>Men's<br>Grooming</td><td>Bravarian<br>Beard Oil</td><td><span class="bottle" role="img" aria-label="Bottle"></span></td><td>AU</td><td>Vitamine E</td><td>Cedarwood</td>
        <td><div class="rate"><i></i><i></i><i></i><i class="off"></i><i class="off"></i></div></td><td><div class="rate"><i></i><i></i><i></i><i></i><i></i></div></td><td><div class="rate"><i></i><i></i><i></i><i></i><i class="off"></i></div></td><td><div class="rate overall"><i></i><i></i><i></i><i class="off"></i><i class="off"></i></div></td><td><span class="buy-btn">GET YOURS NOW</span></td></tr>
      <tr><td>Wellhaven<br>Soaps</td><td>Outbacker's<br>Beard Oil</td><td><span class="bottle" role="img" aria-label="Bottle"></span></td><td>AU</td><td>Almond</td><td>Sandalwood</td>
        <td><div class="rate"><i></i><i></i><i></i><i></i><i class="off"></i></div></td><td><div class="rate"><i></i><i></i><i></i><i class="off"></i><i class="off"></i></div></td><td><div class="rate"><i></i><i></i><i></i><i></i><i></i></div></td><td><div class="rate overall"><i></i><i></i><i></i><i class="off"></i><i class="off"></i></div></td><td><span class="buy-btn">GET YOURS NOW</span></td></tr>
    </tbody>
  </table>
  <div class="abs view-more">View more ...</div>
</main>

<aside class="abs side-box" style="top:238px;height:206px">
  <h3>Popular Posts</h3>
  <div class="post" style="top:37px"><div class="thumb" role="img" aria-label="Beard oil product photo"></div><h4>Misty Ridge Man Beard Oil Papa ...</h4><div class="meta" style="top:24px">BY: <b>Delvin Marsk</b></div><div class="meta" style="top:37px">February 12, 2016</div><div class="rule"></div></div>
  <div class="post" style="top:96px"><div class="thumb" role="img" aria-label="Beard oil product photo"></div><h4>Outbacker's Face/Beard Oil by Wellhaven ...</h4><div class="meta" style="top:24px">BY: <b>Delvin Marsk</b></div><div class="meta" style="top:37px">February 09, 2016</div><div class="rule"></div></div>
  <div class="post" style="top:154px"><div class="thumb" role="img" aria-label="Beard oil product photo"></div><h4>Bravarian Beard Oil by Bravarian ...</h4><div class="meta" style="top:24px">BY: <b>Delvin Marsk</b></div><div class="meta" style="top:37px">January 25, 2016</div></div>
</aside>

<aside class="abs side-box" style="top:456px;height:206px">
  <h3 class="ring">Recent Comments</h3>
  <div class="comment" style="top:36px"><div class="avatar" role="img" aria-label="Commenter photo"></div><h5>PHIL</h5><p>Great reviews, really helpful ! My beard and I thank you lol</p><div class="rule"></div></div>
  <div class="comment" style="top:95px"><div class="avatar" role="img" aria-label="Commenter photo"></div><h5>JAMES</h5><p>My grandfather used this oil, he swore be it</p><div class="rule"></div></div>
  <div class="comment" style="top:153px"><div class="avatar" role="img" aria-label="Commenter photo"></div><h5>ROBERT</h5><p>The misusus loved this oil on my beard !!</p></div>
</aside>

<footer class="abs site-footer wood-dark">
  <div class="abs footer-col" style="left:161px;top:17px"><h6>Quick Links</h6><ul><li>Home</li><li>Review Methedology</li><li>Charter</li><li>Blog</li><li>About Me</li><li>Contact</li></ul></div>
  <div class="abs footer-col" style="left:406px;top:17px"><h6>Subscribe to my newsletter</h6><p>Don't miss out on any of my reviews and offers.</p><span class="email">Enter your email here</span><span class="submit">SUBMIT</span></div>
  <div class="abs footer-col" style="left:678px;top:17px"><h6>Tags</h6><div class="tags"><span>Refreshing</span><span>Afordable</span><span>Cooling</span><span>Comfortable</span><span>Awesome</span><span>Oilly</span></div></div>
  <div class="abs footer-col" style="left:972px;top:14px"><h6>Follow me on</h6><div class="social"><span role="img" aria-label="Social profile 1"></span><span role="img" aria-label="Social profile 2"></span><span role="img" aria-label="Video channel"></span></div></div>
</footer>

<div class="abs copyright">Copyright @ 2016 <i>Top Whisker Tonic</i> -&nbsp; All rights reserved</div>

</body>
</html>
```